Heron Loan Partners Business Card

We need a business card design for our mortgage servicing company. In addition to servicing the loans of homeowners, we help homeowners with purchasing their homes and any mortgage refinancing. We would like to see designs that use the colors in the logo attached below (gold-ish yellow and navy blue), and any other design you deem fit! The design should communicate a simpler life with smart mortgages provided by Heron.

```html
<!DOCTYPE html>
<html lang="en">
<head>
<meta charset="utf-8">
<title>Heron Loan Partners Business Card</title>
<link rel="stylesheet" href="https://fonts.googleapis.com/css2?family=Libre+Baskerville:wght@700&family=Montserrat:wght@400;500&display=swap">
<style>
  :root {
    --backdrop: #1d1d1f;
    --navy: #262050;
    --ink: #231f4a;
    --gold: #deb13c;
    --teal: #2aa5a0;
    --paper: #ffffff;
  }
  * { margin: 0; padding: 0; box-sizing: border-box; }
  html, body { width: 900px; height: 1200px; overflow: hidden; }
  body {
    background: var(--backdrop);
    position: relative;
    font-family: "Montserrat", sans-serif;
  }
  .card {
    position: absolute;
    width: 630px;
    height: 360px;
    box-shadow: 0 10px 24px rgba(0,0,0,0.45);
  }
  .card-front { left: 135px; top: 213px; background: var(--navy); }
  .card-back { left: 135px; top: 627px; background: var(--paper); }

  .brand-name {
    position: absolute;
    left: 0; right: 0;
    text-align: center;
    font-family: "Libre Baskerville", serif;
    font-weight: 700;
    color: var(--gold);
    white-space: nowrap;
  }
  .card-front .brand-name { top: 150px; font-size: 42px; }
  .card-back .brand-name { top: 68px; font-size: 32px; }

  .holder {
    position: absolute;
    right: 328px;
    top: 200px;
    text-align: right;
  }
  .holder-name {
    font-family: "Libre Baskerville", serif;
    font-weight: 700;
    font-size: 21px;
    color: var(--gold);
    white-space: nowrap;
  }
  .holder-role {
    margin-top: 6px;
    font-size: 15px;
    color: var(--ink);
    letter-spacing: 0.5px;
  }
  .divider {
    position: absolute;
    left: 314px;
    top: 188px;
    width: 2px;
    height: 72px;
    background: var(--teal);
  }
  .contacts {
    position: absolute;
    left: 326px;
    top: 190px;
    list-style: none;
  }
  .contacts li {
    display: flex;
    align-items: center;
    height: 24px;
    font-size: 15px;
    color: var(--ink);
    white-space: nowrap;
  }
  .contacts svg { width: 11px; height: 11px; margin-right: 7px; fill: var(--gold); flex: none; }
  .contacts .phone { letter-spacing: 2.2px; }
  .location {
    position: absolute;
    left: 0; right: 0;
    top: 278px;
    text-align: center;
    font-size: 15px;
    color: var(--ink);
    letter-spacing: 0.3px;
  }
  .location svg { display: block; margin: 0 auto 8px; width: 12px; height: 16px; fill: var(--gold); }
</style>
</head>
<body>
  <section class="card card-front">
    <div class="brand-name">Heron Loan Partners</div>
  </section>

  <section class="card card-back">
    <div class="brand-name">Heron Loan Partners</div>

    <div class="holder">
      <div class="holder-name">Dana Whitfield</div>
      <div class="holder-role">Founder</div>
    </div>
    <div class="divider"></div>
    <ul class="contacts">
      <li class="phone">
        <svg viewBox="0 0 24 24"><path d="M6.6 10.8c1.4 2.8 3.8 5.1 6.6 6.6l2.2-2.2c.3-.3.7-.4 1-.2 1.1.4 2.3.6 3.6.6.6 0 1 .4 1 1V20c0 .6-.4 1-1 1C10.6 21 3 13.4 3 4c0-.6.4-1 1-1h3.5c.6 0 1 .4 1 1 0 1.3.2 2.5.6 3.6.1.3 0 .7-.2 1z"/></svg>
        (888)-555-0142
      </li>
      <li>
        <svg viewBox="0 0 24 24"><path d="M2 5h20v14H2z M2 5l10 8 10-8" /></svg>
        info@heronloans.com
      </li>
      <li>
        <svg viewBox="0 0 24 24"><circle cx="12" cy="12" r="10"/></svg>
        www.heronloans.com
      </li>
    </ul>

    <div class="location">
      <svg viewBox="0 0 24 32"><path d="M12 0C5.4 0 0 5.4 0 12c0 9 12 20 12 20s12-11 12-20C24 5.4 18.6 0 12 0zm0 17a5 5 0 1 1 0-10 5 5 0 0 1 0 10z"/></svg>
      418 Bayview Ave S, Clearwater, FL 33756
    </div>
  </section>
</body>
</html>
```